VC Liquidity Transformation Case Study Design

2-Page VC Case Study Brochure Concept
We are looking for visual design concepts, not finished production files.
This project explores a 2-page institutional brochure for Brisket Partners that:
Page 1 → Explains our differentiated approach to venture-backed technology exits
Page 2 → Demonstrates how we convert long-tenured portfolio companies into strategic outcomes
The attached Design Guide includes:
• Page wireframe
• Referenced visuals
• Icon direction
• Tone and design rules
Designers should use this as a structural guide, not a constraint.

- BP Process Diagram: several modifications needed to the images to be recreated (various images attached)
- Brisket Partners 2-Page Brochure small (B1 and Final F1 - psd files) are my current 2 page brochure. Leverage if you'd like.
- Logo package: this is the package of Brisket Partners logos

Target Market(s)

Institutional capital investors like Venture capitalists and private equity groups

Industry/Entity Type

investment banking

Font styles to use
Sans Serif

Colors
0054AA
0677BA
7BADD7
CADEEF
E8F1F8

Requirements
Must have
• See design guide
Nice to have
• See design guide
Should not have
• See design guide

```html
<!DOCTYPE html>
<html lang="en">
<head>
<meta charset="utf-8">
<title>Brisket Partners – VC Liquidity Brochure</title>
<link rel="stylesheet" href="https://fonts.googleapis.com/css2?family=Open+Sans:ital,wght@0,400;0,600;0,700;0,800;1,700&display=swap">
<style>
  :root{
    --navy:#0e2a5c;
    --blue-deep:#0054AA;
    --blue:#0677BA;
    --blue-mid:#7BADD7;
    --blue-soft:#CADEEF;
    --blue-pale:#E8F1F8;
    --ink:#1d2433;
    --quote-grey:#bdbec3;
    --stage:#dcdfe3;
    --white:#ffffff;
    --gold:#e0a13a;
  }
  *{box-sizing:border-box;margin:0;padding:0}
  html,body{width:1200px;height:802px;overflow:hidden}
  body{background:var(--stage);font-family:"Open Sans",Arial,sans-serif;color:var(--ink);position:relative}
  .page{position:absolute;top:100px;width:466px;height:600px;background:var(--white);overflow:hidden}
  .page--approach{left:84px}
  .page--outcome{left:632px;width:463px}
  .page-header{position:absolute;inset:0 0 auto 0;height:150px;background:linear-gradient(180deg,var(--blue-soft) 0%,var(--blue-pale) 55%,var(--white) 100%)}
  .brand{position:absolute;left:18px;top:22px;display:flex;align-items:center;gap:7px}
  .brand-dot{width:28px;height:28px;border-radius:50%;background:var(--navy)}
  .brand-name{font-weight:700;font-size:12px;line-height:1.1;color:var(--navy);letter-spacing:.5px;text-transform:uppercase;width:80px}
  .kicker{position:absolute;left:20px;top:68px;font-size:9.5px;font-weight:700;color:var(--blue-deep)}
  .headline{position:absolute;left:20px;top:80px;font-size:25px;line-height:1.08;font-weight:400;color:var(--blue-deep)}
  .headline strong{font-weight:800;color:var(--navy)}
  .side-title{position:absolute;left:312px;top:24px;width:140px;font-size:16px;line-height:1.12;font-weight:700;color:var(--ink)}
  .side-title span{display:block;font-size:11.5px;font-weight:600;margin-top:2px;line-height:1.18}
  .page--outcome .side-title{left:330px;top:24px;width:120px;font-size:16.5px}
  .panel{position:absolute;border:1.5px solid var(--navy);border-radius:12px;background:var(--white);overflow:hidden}
  .panel svg{display:block}
  .quote-card{position:absolute;left:314px;top:170px;width:127px;height:159px;background:var(--quote-grey);border-radius:10px;padding:26px 12px 0 14px;font-size:14.5px;line-height:1.18;font-weight:600;color:var(--ink)}
  .quote-mark{position:absolute;font-size:36px;font-weight:700;color:var(--navy);line-height:1}
  .quote-mark--open{left:10px;top:-6px}
  .quote-mark--close{right:10px;bottom:-14px}
  .caption{position:absolute;left:0;right:0;text-align:center;font-size:11px;font-weight:700;font-style:italic;color:var(--navy)}
  .panel-title{font-size:11px;font-weight:700;text-align:center;color:var(--ink);margin-top:8px;line-height:1.1}
  .visual{margin:10px auto 0;border-radius:6px}
  .visual-note{font-size:5.5px;color:#555;text-align:center;margin-top:4px}
  .closing-line{position:absolute;left:20px;right:20px;top:548px;text-align:center;font-size:12px;font-weight:700;line-height:1.3;color:var(--ink)}
</style>
</head>
<body>

<section class="page page--approach">
  <div class="page-header"></div>
  <div class="brand"><div class="brand-dot"></div><div class="brand-name">Brisket Partners</div></div>
  <p class="kicker">Unlocking Strategic</p>
  <h1 class="headline">Value from<br><strong>Deep Technology</strong></h1>
  <h2 class="side-title">Helping Venture Investors Transition<span>Long- Held Portfolio Companies into Strategic Outcomes</span></h2>

  <div class="panel" style="left:20px;top:162px;width:278px;height:168px">
    <svg width="275" height="165" viewBox="0 0 275 165">
      <rect x="12" y="10" width="251" height="145" fill="var(--blue-pale)" rx="4"/>
      <text x="24" y="24" font-size="5.5" fill="var(--ink)">Traditional Tech I-Banks</text>
      <text x="165" y="24" font-size="5.5" fill="var(--ink)">Brisket Partners: IP-Led Approach</text>
      <rect x="132" y="30" width="8" height="106" fill="var(--blue-soft)"/>
      <text x="138" y="84" font-size="4.5" fill="var(--navy)" transform="rotate(-90 138 84)" text-anchor="middle">Core IP Catalyst Lens</text>
      <path d="M50 80 l14 -6 l14 6 v16 l-14 6 l-14 -6z" fill="#fff" stroke="var(--blue-mid)" stroke-width=".8"/>
      <text x="64" y="114" font-size="5.5" fill="var(--ink)" text-anchor="middle">Niche IP Company</text>
      <text x="64" y="121" font-size="4" fill="#555" text-anchor="middle">Operations | Sales &amp; Marketing | R&amp;D</text>
      <g stroke="var(--blue-mid)" stroke-width=".6">
        <rect x="165" y="56" width="60" height="16" fill="var(--blue-mid)"/>
        <rect x="165" y="74" width="60" height="18" fill="var(--blue-soft)"/>
        <rect x="165" y="94" width="60" height="18" fill="#fff"/>
      </g>
      <text x="195" y="66" font-size="5" fill="#fff" text-anchor="middle">Core IP Catalyst</text>
      <text x="195" y="85" font-size="4.5" fill="var(--navy)" text-anchor="middle">Economic Value of Niche IP</text>
      <text x="195" y="105" font-size="4.5" fill="var(--navy)" text-anchor="middle">Niche IP Company</text>
      <line x1="12" y1="140" x2="263" y2="140" stroke="var(--blue-mid)" stroke-width=".5"/>
      <text x="30" y="150" font-size="5.5" fill="var(--ink)">Value Focus</text>
      <text x="180" y="150" font-size="5.5" fill="var(--ink)">Value Focus with IP</text>
    </svg>
  </div>

  <blockquote class="quote-card">
    <span class="quote-mark quote-mark--open">“</span>
    Strategic buyers acquire capability acceleration, not revenue history.
    <span class="quote-mark quote-mark--close">”</span>
  </blockquote>

  <div class="panel" style="left:20px;top:360px;width:424px;height:198px">
    <svg width="421" height="195" viewBox="0 0 421 195">
      <defs><linearGradient id="band"><stop offset="0" stop-color="var(--blue)"/><stop offset="1" stop-color="var(--blue-soft)"/></linearGradient></defs>
      <text x="210" y="26" font-size="15" font-weight="800" text-anchor="middle" fill="var(--navy)">VENTURE LIFECYCLE <tspan fill="var(--blue-deep)">POSITIONING</tspan></text>
      <text x="210" y="40" font-size="8" font-weight="700" text-anchor="middle" fill="var(--ink)">Unlocking Strategic Value from Deep Technology</text>
      <text x="210" y="50" font-size="6.5" text-anchor="middle" fill="#555">Helping Venture Investors Transition Long-Held Portfolio Companies</text>
      <rect x="30" y="135" width="60" height="20" fill="var(--blue-pale)"/>
      <rect x="90" y="122" width="62" height="33" fill="var(--blue-soft)"/>
      <rect x="152" y="110" width="68" height="45" fill="var(--blue-mid)" opacity=".55"/>
      <rect x="220" y="92" width="74" height="63" fill="var(--blue-deep)"/>
      <rect x="294" y="100" width="70" height="55" fill="var(--blue-pale)"/>
      <path d="M130 112 q120 -50 250 -36" fill="none" stroke="var(--gold)" stroke-width="1.4" stroke-dasharray="3 2"/>
      <polygon points="382,76 374,72 375,80" fill="var(--gold)"/>
      <rect x="232" y="68" width="58" height="13" rx="2" fill="var(--navy)"/>
      <text x="261" y="77" font-size="5.8" fill="#fff" text-anchor="middle">Brisket Engages Here</text>
      <g fill="var(--blue-deep)"><rect x="48" y="116" width="4" height="12"/><rect x="54" y="110" width="4" height="18"/><rect x="60" y="104" width="4" height="24"/></g>
      <circle cx="121" cy="110" r="7" fill="none" stroke="var(--blue)" stroke-width="2.5"/>
      <polygon points="186,92 196,108 176,108" fill="none" stroke="var(--navy)" stroke-width="1.6"/>
      <text x="186" y="106" font-size="8" font-weight="700" text-anchor="middle" fill="var(--navy)">!</text>
      <circle cx="257" cy="108" r="8" fill="none" stroke="#fff" stroke-width="1.4"/><circle cx="257" cy="108" r="3" fill="#fff"/>
      <circle cx="330" cy="90" r="8" fill="#d9b36b"/>
      <g font-size="6.5" font-weight="700" fill="var(--navy)" text-anchor="middle">
        <text x="60" y="150">EARLY GROWTH</text><text x="121" y="150">SCALING</text><text x="186" y="150">PLATEAU</text>
        <text x="257" y="138" fill="#fff">STRATEGIC</text><text x="257" y="146" fill="#fff">TRANSITION</text><text x="330" y="118">LIQUIDITY</text>
      </g>
      <rect x="30" y="160" width="364" height="12" fill="url(#band)"/>
      <g font-size="6" fill="#fff" text-anchor="middle"><text x="62" y="168">EARLY Growth</text><text x="155" y="168">Strategic</text><text x="257" y="168">Strategic Transition</text><text x="345" y="168" fill="var(--navy)">Liquidity</text></g>
    </svg>
  </div>
  <p class="caption" style="top:570px">Subtle upward arc from Strategic Transition to Liquidity</p>
</section>

<section class="page page--outcome">
  <div class="page-header"></div>
  <div class="brand"><div class="brand-dot"></div><div class="brand-name">Brisket Partners</div></div>
  <p class="kicker">From Long-</p>
  <h1 class="headline">Tenured Holding to<br><strong>Strategic Outcome</strong></h1>
  <h2 class="side-title">How Brisket Enables Venture Capital Recycling</h2>

  <div class="panel" style="left:18px;top:158px;width:160px;height:166px">
    <p class="panel-title">The Challenge</p>
    <div class="visual" role="img" aria-label="Portfolio reality diagram comparing traditional focus with overlooked IP value" style="width:130px;height:96px;background:linear-gradient(135deg,var(--blue-pale),var(--blue-soft))"></div>
    <p class="visual-note">Unlocking value from the overlooked majority</p>
  </div>
  <div class="panel" style="left:185px;top:158px;width:83px;height:166px">
    <p class="panel-title">Brisket<br>Intervention</p>
    <div class="visual" role="img" aria-label="Intervention flow from core IP catalyst to strategic positioning" style="width:62px;height:104px;margin-top:6px;background:linear-gradient(180deg,var(--blue-pale),var(--blue-soft))"></div>
  </div>
  <div class="panel" style="left:272px;top:158px;width:170px;height:166px">
    <p class="panel-title">Process Outcome</p>
    <div class="visual" role="img" aria-label="Outcome icons: buyer engagement, competitive process, accelerated closing, strategic liquidity" style="width:146px;height:96px;background:linear-gradient(135deg,var(--white),var(--blue-pale))"></div>
    <p class="visual-note">Unlocking value from the overlooked majority</p>
  </div>

  <div class="panel" style="left:18px;top:340px;width:424px;height:198px">
    <svg width="421" height="195" viewBox="0 0 421 195">
      <rect x="50" y="8" width="300" height="176" fill="var(--blue-pale)" rx="4"/>
      <text x="200" y="22" font-size="7" letter-spacing="1.5" text-anchor="middle" fill="var(--ink)">BOTTOM SECTION — <tspan fill="var(--blue-deep)" font-weight="700">IMPACT</tspan></text>
      <text x="200" y="35" font-size="7.5" font-weight="700" text-anchor="middle" fill="var(--navy)">Transforming Plateau Companies Into Strategic Exits &amp; Recycled Capital</text>
      <g fill="#fff" stroke="var(--blue-mid)" stroke-width="1"><circle cx="95" cy="78" r="32"/><circle cx="200" cy="74" r="34"/><circle cx="305" cy="78" r="32"/></g>
      <g stroke="var(--blue)" stroke-width="1.2" fill="none"><path d="M129 76 h30"/><path d="M236 76 h30"/></g>
      <polygon points="164,76 158,73 158,79" fill="var(--blue)"/><polygon points="271,76 265,73 265,79" fill="var(--blue)"/>
      <g font-size="5" font-weight="700" text-anchor="middle" fill="var(--navy)"><text x="95" y="77">PLATEAUED COMPANY</text><text x="200" y="73">BRISKET ENGAGEMENT</text><text x="305" y="77">STRATEGIC EXITS</text></g>
      <g font-size="4.3" text-anchor="middle" fill="#555"><text x="95" y="85">Stagnation &amp; Limited Options</text><text x="200" y="81">Core IP Catalyst</text><text x="305" y="85">Maximized Value Realized</text></g>
      <line x1="60" y1="118" x2="340" y2="118" stroke="var(--blue-soft)"/>
      <text x="62" y="140" font-size="5.5" font-weight="700" fill="var(--navy)">OUTCOMES:</text>
      <g fill="#fff" stroke="var(--blue)" stroke-width=".8"><circle cx="120" cy="138" r="7"/><circle cx="185" cy="138" r="7"/><circle cx="245" cy="138" r="7"/><circle cx="300" cy="138" r="7"/></g>
      <g font-size="5" fill="var(--ink)"><text x="130" y="137">Capital</text><text x="130" y="143">Returned</text><text x="195" y="137">Portfolio</text><text x="195" y="143">Refreshed</text><text x="255" y="137">IP Value</text><text x="255" y="143">Unlocked</text><text x="310" y="137">New Funds/</text><text x="310" y="143">Investments</text></g>
      <text x="200" y="170" font-size="7" text-anchor="middle" fill="var(--ink)">Brisket transforms stagnation into <tspan font-weight="700" fill="var(--navy)">strategic liquidity.</tspan></text>
    </svg>
  </div>
  <p class="closing-line">Aligning IP-rich companies with strategic demand unlocks liquidity where traditional exits stall.</p>
</section>

</body>
</html>
```